Event Center Website

We need a new website design for an upscale event center in Reno, Nevada. The building hosts everything from weddings to corporate events to funerals and it competitively more expensive. The overall look and feel is consistent with a Lake Tahoe aesthetic. The current site can be viewed at www.themaplehallevents.com. They are looking for a major upgrade. A sample site they like is www.cliffsidelodgestay.com. We have new photography available (some attached). The site should be very visual. A site map is attached as well for direction on what elements the site should include as well as labels for navigation. I am looking for a home page and sample interior page. Any questions, let me know. Thanks.
Updates

I have added some photography of the center itself for use rather than stock photography. Thanks!

Target Market(s)

Brides, professionals, high-income

Industry/Entity Type

Building

Requirements
Must have
• See site map

```html
<!DOCTYPE html>
<html lang="en">
<head>
<meta charset="utf-8">
<title>Meet Our Team – The Maple Hall</title>
<link href="https://fonts.googleapis.com/css2?family=Ubuntu:wght@400;500;700&display=swap" rel="stylesheet">
<style>
:root{
  --brown-dark:#4a2812;
  --brown:#5a3318;
  --rust:#b0602a;
  --orange:#c97a1e;
  --orange-deep:#84460c;
  --cream:#f5e8c6;
  --cream-light:#f1e9d7;
  --white:#ffffff;
  --text:#3a2414;
}
*{margin:0;padding:0;box-sizing:border-box}
html,body{width:1200px;height:945px;overflow:hidden}
body{font-family:"Ubuntu",sans-serif;color:var(--text);background:var(--white);position:relative}
.hero{position:absolute;left:0;top:0;width:1200px;height:157px;
  background:linear-gradient(90deg,#7a4a1a 0%,#c8902e 22%,#e8d7b8 42%,#6b3f18 50%,#e8d7b8 58%,#c8902e 78%,#7a4a1a 100%)}
.util-nav{position:absolute;left:849px;top:0;width:227px;height:52px;background:var(--brown-dark);
  display:flex;align-items:center;justify-content:center;gap:22px;color:#fff;font-size:15px}
.util-nav .sep{width:1px;height:26px;background:#fff}
.main-nav{position:absolute;left:100px;top:52px;width:976px;height:58px;background:var(--cream);
  display:flex;align-items:center}
.brand{width:190px;padding-left:10px;font-size:21px;font-weight:500;color:var(--brown-dark);display:flex;align-items:center;gap:7px}
.brand .dot{width:10px;height:10px;border-radius:50%;background:var(--rust)}
.main-nav ul{list-style:none;display:flex;gap:34px;font-size:15px;font-weight:500;color:var(--brown-dark)}
.title-band{position:absolute;left:0;top:157px;width:1200px;height:71px;background:var(--cream-light);
  border-bottom:2px solid var(--brown)}
.title-band h1{position:absolute;left:124px;top:19px;font-size:27px;font-weight:500;color:var(--brown-dark)}
.crumbs{position:absolute;right:125px;top:28px;font-size:16px;font-weight:500;color:var(--brown-dark)}
.crumbs span{color:var(--rust)}
.section-title{position:absolute;left:0;top:253px;width:1200px;text-align:center;font-size:36px;font-weight:500;color:var(--brown-dark)}
.section-rule{position:absolute;left:563px;top:308px;width:75px;height:2px;background:var(--brown)}
.member-name{position:absolute;left:124px;top:320px;font-size:26px;font-weight:500;color:var(--brown-dark)}
.member-role{position:absolute;left:124px;top:352px;font-size:22px;color:var(--rust)}
.member-rule{position:absolute;left:124px;top:388px;width:952px;height:2px;background:var(--brown)}
.portrait{position:absolute;left:124px;top:417px;width:382px;height:312px;border:2px solid var(--brown);
  background:radial-gradient(ellipse at 55% 55%,#d8cfc6 0%,#eeeae6 45%,#ffffff 75%)}
.bio{position:absolute;left:537px;top:418px;width:538px;font-size:14px;line-height:24.9px;text-align:justify;color:var(--text)}
.footer{position:absolute;left:0;top:777px;width:1200px;height:168px;background:var(--cream)}
.signup{position:absolute;left:131px;top:41px;width:340px;height:60px;background:var(--orange-deep);display:flex;align-items:center;color:#fff}
.signup .label{flex:1;padding-left:9px;font-size:15px}
.signup svg{margin-right:10px}
.signup .send{width:56px;height:100%;background:var(--orange);display:flex;align-items:center;justify-content:center;font-size:15px}
.contact{position:absolute;left:495px;top:42px;width:362px;height:58px;background:var(--brown-dark);border-radius:3px;display:flex;color:#fff;font-size:13px}
.contact .addr{width:150px;padding:10px 0 0 11px;line-height:21px;border-right:1px solid #7a5030}
.contact .lines{padding:8px 0 0 9px;line-height:24px}
.contact .lines b{font-weight:400;color:var(--orange);margin-right:5px}
.social{position:absolute;left:887px;top:42px;width:189px;height:60px;background:var(--brown-dark);border-radius:3px;display:flex;align-items:center;justify-content:center;gap:12px}
.social span{width:29px;height:29px;display:block}
.footer-nav{position:absolute;left:0;top:128px;width:1200px;display:flex;justify-content:center;gap:29px;list-style:none;font-size:14px;color:var(--brown-dark)}
</style>
</head>
<body>
<div class="hero" role="img" aria-label="Photo of the event hall ceiling with draped fabric and a chandelier"></div>
<nav class="util-nav"><span>FAQ</span><span class="sep"></span><span>TESTIMONIAL</span></nav>
<header class="main-nav">
  <div class="brand"><span class="dot"></span>The Maple Hall</div>
  <ul><li>ABOUT US</li><li>GALLERY</li><li>WEDDING</li><li>MEETINGS</li><li>OTHER EVENTS</li><li>CATERING</li><li>MENUS</li></ul>
</header>
<div class="title-band"><h1>MEET OUR TEAM</h1><div class="crumbs">HOME / <span>MEET OUR TEAM</span></div></div>
<h2 class="section-title">Meet Our Team</h2>
<div class="section-rule"></div>
<h3 class="member-name">Marlowe</h3>
<div class="member-role">Chef</div>
<div class="member-rule"></div>
<div class="portrait" role="img" aria-label="Portrait photo of the chef in a grey t-shirt"></div>
<p class="bio">Raised in Northern Nevada, Marlowe always loved cooking and entertaining. It wasn’t until after college that she considered a career in the kitchen. After completing her degree in Anthropology from Sierra State University, she enrolled in the Bayview Culinary Institute in San Francisco where she gained a foundation in French technique. Since, she has worked San Francisco at the Harbor Point House, as an Event Planner for Alder Lane Catering in Portland, as a Manager for Summit Street Cafe in Denver, and most recently as the Catering Chef for The Copper Table in Reno. Her passion is experimenting with new cuisine and ingredients and her style is usually lighter and healthier dishes using seasonal ingredients, although she is not afraid to experiment with sugar and new dessert recipes! Marlowe and her husband welcomed their first baby last year, and she has found cooking to be a whole new challenge. As her daughter grows she hopes she will like helping in the kitchen and that she can instill the importance of a balanced diet and bringing the family together around the dinner table</p>
<footer class="footer">
  <div class="signup">
    <span class="label">ENTER YOUR EMAIL</span>
    <svg width="32" height="30" viewBox="0 0 32 30" aria-hidden="true"><path d="M2 12 L16 2 L30 12 V28 H2 Z" fill="#fff" stroke="#84460c"/><path d="M2 12 L16 21 L30 12 M2 28 L13 19 M30 28 L19 19" fill="none" stroke="#84460c" stroke-width="1.3"/></svg>
    <span class="send">SEND</span>
  </div>
  <div class="contact">
    <div class="addr">48 Cedar Ridge Road<br>Reno, NV 89511</div>
    <div class="lines"><b>Phone:</b>775-555-0142<br><b>Email:</b>info@themaplehallevents.com</div>
  </div>
  <div class="social">
    <span style="background:#3b5a98"></span><span style="background:#27a4dd"></span><span style="background:#c4302b"></span><span style="background:#f7931e"></span>
  </div>
  <ul class="footer-nav"><li>ABOUT US</li><li>GALLERY</li><li>WEDDING</li><li>MEETINGS</li><li>OTHER EVENTS</li><li>CATERING</li><li>MENUS</li></ul>
</footer>
</body>
</html>
```